Presentation Folder with inside Pockets

We need a Presentation Folder with inside pockets. The size of the folder will be 9" x 12" and will be printed on the cover, the back and the inside folder flaps. The design will be very simple and consist of our logo (large) on the front cover and our logo (smaller) and contact information on the back. We are open to various colors that you think may go along with our logo. When you display your work, show the front, back and inside.

Target Market(s)

Pharmaceutical Companies

Industry/Entity Type

Work

Requirements
Should not have
• please do not add stock medical photos.

```html
<!DOCTYPE html>
<html lang="en">
<head>
<meta charset="utf-8">
<title>Meridian Trials Inc. – Presentation Folder</title>
<link rel="stylesheet" href="https://fonts.googleapis.com/css2?family=Open+Sans:wght@400;600;700&display=swap">
<style>
  :root{
    --stage:#000000;
    --paper:#f7f7f7;
    --paper-shade:#e9e9e9;
    --green-light:#9ccc3c;
    --green:#6aa33a;
    --green-dark:#4f8a34;
    --blue-rule:#1f5f9a;
    --ink:#111111;
    --ink-soft:#444444;
    --spine:#cfcfcf;
    --white:#ffffff;
  }
  *{box-sizing:border-box;margin:0;padding:0}
  html,body{width:1200px;height:979px;overflow:hidden;background:var(--stage)}
  body{font-family:"Open Sans",Arial,sans-serif;position:relative}
  .folder-art{position:absolute;left:0;top:0}
  .brand{position:absolute;display:flex;align-items:center;gap:14px}
  .brand__dot{border-radius:50%;background:var(--green)}
  .brand__name{font-weight:700;color:var(--ink);line-height:1.05;text-align:center;letter-spacing:.02em}
  .brand--cover{left:660px;top:78px}
  .brand--cover .brand__dot{width:66px;height:66px}
  .brand--cover .brand__name{font-size:30px}
  .brand--back{left:187px;top:576px}
  .brand--back .brand__dot{width:58px;height:58px}
  .brand--back .brand__name{font-size:25px}
  .contact{position:absolute;color:var(--white);font-size:11px;line-height:16px}
  .contact--left{left:116px;top:676px}
  .contact--left div{display:flex;align-items:center;gap:5px}
  .contact--right{right:605px;top:676px;text-align:right}
  .web{position:absolute;left:605px;width:510px;top:690px;text-align:center;color:var(--white);font-size:13px;letter-spacing:.2em}
  .card{position:absolute;width:199px;height:113px;background:var(--white);border:1px solid #d6d6d6;color:var(--ink)}
  .card--left{left:240px;top:777px}
  .card--right{left:784px;top:777px}
  .card__brand{position:absolute;left:10px;top:12px;display:flex;align-items:center;gap:5px}
  .card__brand .brand__dot{width:14px;height:14px}
  .card__brand .brand__name{font-size:7.5px}
  .card__lines{position:absolute;left:11px;top:64px;font-size:5.5px;line-height:8px;color:var(--ink-soft)}
  .card__lines div{display:flex;align-items:center;gap:3px}
  .card__addr{position:absolute;left:11px;top:91px;font-size:5.5px;line-height:7px;color:var(--ink-soft)}
  .card__person{position:absolute;left:138px;top:67px;font-size:6.5px;line-height:8px;text-align:center;color:var(--ink)}
</style>
</head>
<body>
<svg class="folder-art" width="1200" height="979" viewBox="0 0 1200 979" aria-hidden="true">
  <defs>
    <linearGradient id="paperFill" x1="0" y1="0" x2="1" y2="1">
      <stop offset="0" stop-color="#ffffff"/>
      <stop offset="1" stop-color="#ececec"/>
    </linearGradient>
    <radialGradient id="bandFill" cx="0.5" cy="0.55" r="0.6">
      <stop offset="0" stop-color="var(--green-light)"/>
      <stop offset="1" stop-color="var(--green-dark)"/>
    </radialGradient>
    <radialGradient id="pocketGreen" cx="0.45" cy="0.4" r="0.6">
      <stop offset="0" stop-color="var(--green-light)"/>
      <stop offset="1" stop-color="var(--green-dark)"/>
    </radialGradient>
    <radialGradient id="pocketGrey" cx="0.45" cy="0.35" r="0.65">
      <stop offset="0" stop-color="#ffffff"/>
      <stop offset="1" stop-color="#d9d9d9"/>
    </radialGradient>
  </defs>
  <!-- outer panels -->
  <rect class="panel" x="97" y="34" width="1018" height="681" fill="url(#paperFill)"/>
  <line class="spine" x1="605" y1="34" x2="605" y2="644" stroke="var(--spine)" stroke-width="1"/>
  <path class="band" d="M97,636 Q330,700 605,644 Q880,700 1115,636 L1115,715 L97,715 Z" fill="url(#bandFill)"/>
  <path class="band-rule" d="M97,636 Q330,700 605,644 Q880,700 1115,636" fill="none" stroke="var(--blue-rule)" stroke-width="3"/>
  <!-- pockets -->
  <path class="pocket pocket--left" d="M52,715 L605,715 C600,800 598,880 590,915 Q585,938 560,938 L110,938 L52,915 Z" fill="url(#pocketGrey)"/>
  <path class="pocket pocket--right" d="M608,715 L1115,715 L1158,727 L1158,915 L1095,938 L640,938 Q625,938 622,915 C615,880 612,800 608,715 Z" fill="url(#pocketGreen)"/>
  <!-- card slits -->
  <g class="card-slits" stroke="#9a9a9a" stroke-width="1">
    <line x1="226" y1="767" x2="252" y2="791"/><line x1="453" y1="767" x2="427" y2="791"/>
    <line x1="226" y1="900" x2="252" y2="876"/><line x1="453" y1="900" x2="427" y2="876"/>
  </g>
  <g class="card-slits" stroke="#3f6f2a" stroke-width="1">
    <line x1="770" y1="767" x2="796" y2="791"/><line x1="997" y1="767" x2="971" y2="791"/>
    <line x1="770" y1="900" x2="796" y2="876"/><line x1="997" y1="900" x2="971" y2="876"/>
  </g>
</svg>

<div class="brand brand--cover">
  <span class="brand__dot"></span>
  <span class="brand__name">MERIDIAN TRIALS<br>INC.</span>
</div>

<div class="brand brand--back">
  <span class="brand__dot"></span>
  <span class="brand__name">MERIDIAN TRIALS<br>INC.</span>
</div>

<div class="contact contact--left">
  <div><svg width="10" height="10" viewBox="0 0 10 10"><circle cx="5" cy="5" r="4.3" fill="none" stroke="#fff" stroke-width="1"/><path d="M3.4,3 L4.3,3 L4.5,4.2 L4,4.6 Q4.8,5.8 5.6,6.1 L6,5.6 L7.1,5.8 L7.1,6.7 Q4,7.2 3.4,3 Z" fill="#fff"/></svg>+1-555-010-4420</div>
  <div><svg width="10" height="10" viewBox="0 0 10 10"><rect x="1" y="2.5" width="8" height="5.5" fill="#fff"/><path d="M1,2.5 L5,5.5 L9,2.5" fill="none" stroke="var(--green)" stroke-width="0.8"/></svg>hello@meridtrials.net</div>
</div>

<div class="contact contact--right">
  <div>Meridian Trials</div>
  <div>Inc. 52 Birch Lane, Lakeview, NY 10987</div>
</div>

<div class="web">www.meridtrials.net</div>

<div class="card card--left">
  <div class="card__brand"><span class="brand__dot"></span><span class="brand__name">MERIDIAN TRIALS<br>INC.</span></div>
  <div class="card__lines">
    <div>&#9742; +1-555-010-4420</div>
    <div>&#9993; hello@meridtrials.net</div>
  </div>
  <div class="card__addr">Meridian Trials, Inc. 52 Birch Lane<br>Lakeview, NY 10987</div>
  <div class="card__person">Your Name<br>Title</div>
</div>

<div class="card card--right">
  <div class="card__brand"><span class="brand__dot"></span><span class="brand__name">MERIDIAN TRIALS<br>INC.</span></div>
  <div class="card__lines">
    <div>&#9742; +1-555-010-4420</div>
    <div>&#9993; hello@meridtrials.net</div>
  </div>
  <div class="card__addr">Meridian Trials, Inc. 52 Birch Lane<br>Lakeview, NY 10987</div>
  <div class="card__person">Your Name<br>Title</div>
</div>
</body>
</html>
```